4th Generation Family Business Needs a New Card Design!

We are a family owned 4th Generation company. We are based in the Sydney, Australia area and we are desperately in need of a more modern and classy card. We are monumental masons who design, supply & erect lasting memorials throughout cemeteries in Sydney. Our customers are normally in a period of grieving. I have attached logo files that will need to be implemented on the card. Company was established 1935. Australian Owned and Operated. Card needs to be designed to PIXO.com specification.

Target Market(s)

Our target market is based upon people that a grieving for family members that have passed away. We also deal with alot of companies that own and operate cemeteries.

Industry/Entity Type

Business

Contact Information for Business Card

Simon Harcourt, Operations Manager, 0417293086, simon@harcourtmemorials.com.au
Lewis Harcourt, Director, 0491630572, lewis@harcourtmemorials.com.au
Phone # 02 9561 3048
Website: www.harcourtmemorials.com.au
Address: Suite 17, 8 Palfrey Lane, West Carlow, Sydney NSW 2156

Font styles to use
Serif
Decorative
Script

Requirements
Must have
• Would like to see the logo nicely implemented with a modern design. Embossed lettering would be a nice additive.

```html
<!DOCTYPE html>
<html lang="en">
<head>
<meta charset="utf-8">
<title>Harcourt Memorials – Business Card</title>
<link href="https://fonts.googleapis.com/css2?family=Arimo:wght@400;700&display=swap" rel="stylesheet">
<style>
  :root {
    --stage: #3a3a3c;
    --stage-edge: #1c1c1e;
    --card-white: #ffffff;
    --card-dark: #1f1f21;
    --card-dark-soft: #2b2b2d;
    --gold: #f0b41c;
    --ink: #1d1d1f;
    --ink-soft: #5a5a5c;
  }
  * { box-sizing: border-box; margin: 0; padding: 0; }
  html, body { width: 1200px; height: 950px; overflow: hidden; }
  body {
    background: radial-gradient(ellipse at 50% 45%, var(--stage) 0%, var(--stage-edge) 100%);
    font-family: "Arimo", Arial, sans-serif;
    position: relative;
  }
  .card {
    position: absolute;
    left: 290px;
    width: 620px;
    height: 379px;
    box-shadow: 0 18px 40px rgba(0,0,0,.55);
    overflow: hidden;
    background: var(--card-white);
  }
  .card--front { top: 70px; }
  .card--back { top: 501px; }

  .brand {
    position: absolute;
    display: flex;
    align-items: center;
    justify-content: center;
    gap: 14px;
    font-family: "Arimo", Arial, sans-serif;
    font-weight: 700;
    line-height: 1;
  }
  .brand__mark {
    width: 22px;
    height: 22px;
    background: var(--gold);
    flex: none;
  }
  .brand__name { white-space: nowrap; }

  .card--front .brand {
    left: 0; right: 0; top: 172px;
    color: var(--ink);
  }
  .card--front .brand__name { font-size: 36px; }

  .back__panel { position: absolute; inset: 0; }
  .card--back .brand {
    left: 0; width: 300px; top: 180px;
    color: var(--card-white);
    gap: 10px;
  }
  .card--back .brand__mark { width: 16px; height: 16px; }
  .card--back .brand__name { font-size: 24px; }

  .contact {
    position: absolute;
    right: 30px;
    top: 66px;
    text-align: right;
    color: var(--ink-soft);
    font-size: 15px;
    line-height: 1.45;
  }
  .contact__name { color: var(--ink); font-weight: 700; font-size: 20px; line-height: 1.2; }
  .contact__role { color: var(--gold); font-size: 16px; margin-bottom: 10px; }
  .contact__row { display: flex; justify-content: flex-end; align-items: center; gap: 8px; }
  .contact__row svg { width: 14px; height: 14px; fill: var(--ink); flex: none; }
  .contact__links { margin-top: 22px; }
</style>
</head>
<body>

<section class="card card--front" aria-label="Card front">
  <div class="brand">
    <span class="brand__mark" aria-hidden="true"></span>
    <span class="brand__name">HARCOURT MEMORIALS</span>
  </div>
</section>

<section class="card card--back" aria-label="Card back">
  <svg class="back__panel" viewBox="0 0 620 379" preserveAspectRatio="none" aria-hidden="true">
    <polygon points="0,0 300,0 352,379 0,379" fill="var(--card-dark-soft)"/>
    <polygon points="0,0 290,0 340,379 0,379" fill="var(--card-dark)"/>
  </svg>

  <div class="brand">
    <span class="brand__mark" aria-hidden="true"></span>
    <span class="brand__name">HARCOURT MEMORIALS</span>
  </div>

  <div class="contact">
    <p class="contact__name">Simon Harcourt</p>
    <p class="contact__role">Operations Manager</p>
    <p class="contact__row">Suite 17, 8 Palfrey Lane<svg viewBox="0 0 14 14"></svg></p>
    <p class="contact__row">West Carlow, Sydney NSW 2156<svg viewBox="0 0 14 14"></svg></p>
    <p class="contact__row">02 9561 3048
      <svg viewBox="0 0 14 14"><path d="M3 1h2l1 3-1.5 1a7 7 0 0 0 4.5 4.5L10 8l3 1v2a2 2 0 0 1-2 2A10 10 0 0 1 1 3a2 2 0 0 1 2-2z"/></svg>
    </p>
    <p class="contact__row">0417293086
      <svg viewBox="0 0 14 14"><path d="M4 0h6a1 1 0 0 1 1 1v12a1 1 0 0 1-1 1H4a1 1 0 0 1-1-1V1a1 1 0 0 1 1-1zm0 2v9h6V2z"/></svg>
    </p>
    <div class="contact__links">
      <p class="contact__row">simon@harcourtmemorials.com.au
        <svg viewBox="0 0 14 14"><path d="M1 3h12v8H1zm1 1 5 4 5-4z" fill-rule="evenodd"/></svg>
      </p>
      <p class="contact__row">www.harcourtmemorials.com.au
        <svg viewBox="0 0 14 14"><circle cx="7" cy="7" r="6"/></svg>
      </p>
    </div>
  </div>
</section>

</body>
</html>
```